Business card for a new cabinet shop company named Veloran Cabinets for high end cabinets

Design a business card, thinking dark rich green with colours to speak of high end luxury ie; cream, gold, black possibly

Mitchell Tarrowby
Director Craftsman
Email: info@veloranjoinery-example.com.au
Instagram : @veloran.cabinets

```html
<!DOCTYPE html>
<html lang="en">
<head>
<meta charset="utf-8">
<title>Veloran Cabinets – Business Card</title>
<link href="https://fonts.googleapis.com/css2?family=Montserrat:wght@400;500;700&display=swap" rel="stylesheet">
<style>
  :root {
    --backdrop: #9a9a9a;
    --card: #132a20;
    --gold: #c9a86a;
    --cream: #f1ece0;
    --silver: #e8e4d8;
  }
  * { box-sizing: border-box; margin: 0; padding: 0; }
  html, body {
    width: 1200px;
    height: 1108px;
    overflow: hidden;
    background: var(--backdrop);
    font-family: "Montserrat", Arial, sans-serif;
  }
  .card {
    position: absolute;
    left: 242px;
    width: 715px;
    height: 409px;
    background: var(--card);
    border-radius: 38px;
  }
  .card--front { top: 119px; }
  .card--back { top: 580px; }

  /* Front */
  .front-brand {
    position: absolute;
    inset: 0;
    display: flex;
    align-items: center;
    justify-content: center;
    gap: 36px;
    padding-bottom: 20px;
  }
  .front-brand__square {
    width: 150px;
    height: 150px;
    border: 5px solid var(--silver);
  }
  .front-brand__name {
    font-size: 46px;
    font-weight: 500;
    color: var(--silver);
    letter-spacing: 0.5px;
  }

  /* Back */
  .back-brand {
    position: absolute;
    left: 43px;
    top: 162px;
    display: flex;
    align-items: center;
    gap: 18px;
  }
  .back-brand__square {
    width: 70px;
    height: 70px;
    border: 3px solid var(--gold);
  }
  .back-brand__name {
    font-size: 30px;
    font-weight: 500;
    line-height: 1.1;
    color: var(--gold);
  }
  .divider {
    position: absolute;
    left: 345px;
    top: 81px;
    width: 2px;
    height: 247px;
    background: var(--gold);
  }
  .contact {
    position: absolute;
    left: 366px;
    top: 78px;
    color: var(--cream);
  }
  .contact__name {
    font-size: 30px;
    font-weight: 700;
    color: var(--gold);
    line-height: 1.2;
    white-space: nowrap;
  }
  .contact__role {
    font-size: 17px;
    margin-top: 4px;
  }
  .contact__address {
    font-size: 17px;
    line-height: 29px;
    margin-top: 18px;
  }
  .contact__list {
    list-style: none;
    margin-top: 12px;
  }
  .contact__item {
    display: flex;
    align-items: center;
    gap: 9px;
    font-size: 16px;
    height: 28.5px;
    white-space: nowrap;
  }
  .contact__icon {
    width: 15px;
    height: 15px;
    flex: none;
  }
</style>
</head>
<body>
  <section class="card card--front">
    <div class="front-brand">
      <div class="front-brand__square"></div>
      <div class="front-brand__name">Veloran Cabinets</div>
    </div>
  </section>

  <section class="card card--back">
    <div class="back-brand">
      <div class="back-brand__square"></div>
      <div class="back-brand__name">Veloran<br>Cabinets</div>
    </div>

    <div class="divider"></div>

    <div class="contact">
      <div class="contact__name">Mitchell Tarrowby</div>
      <div class="contact__role">Director Craftsman</div>
      <div class="contact__address">Your address, City<br>State, Zip 1234</div>
      <ul class="contact__list">
        <li class="contact__item">
          <svg class="contact__icon" viewBox="0 0 16 16" aria-hidden="true">
            <path d="M1 6 Q8 1 15 6 L13 8 L11 6.5 L5 6.5 L3 8 Z" fill="#c9a86a"/>
            <rect x="3" y="8.5" width="10" height="6" rx="1" fill="#c9a86a"/>
          </svg>
          <span>123 456 789</span>
        </li>
        <li class="contact__item">
          <svg class="contact__icon" viewBox="0 0 16 16" aria-hidden="true">
            <rect x="1" y="3.5" width="14" height="9" fill="#c9a86a"/>
            <path d="M1 3.5 L8 9 L15 3.5" fill="none" stroke="#132a20" stroke-width="1.2"/>
          </svg>
          <span>info@veloranjoinery-example.com.au</span>
        </li>
        <li class="contact__item">
          <svg class="contact__icon" viewBox="0 0 16 16" aria-hidden="true">
            <circle cx="8" cy="8" r="6.5" fill="none" stroke="#c9a86a" stroke-width="1.6"/>
          </svg>
          <span>@veloran.cabinets</span>
        </li>
        <li class="contact__item">
          <svg class="contact__icon" viewBox="0 0 16 16" aria-hidden="true">
            <circle cx="8" cy="8" r="7" fill="#c9a86a"/>
            <path d="M1 8 H15 M8 1 Q4 8 8 15 M8 1 Q12 8 8 15" fill="none" stroke="#132a20" stroke-width="1"/>
          </svg>
          <span>www.veloran-example.com.au</span>
        </li>
      </ul>
    </div>
  </section>
</body>
</html>
```